Speisekarten-Design für Tennis- und Freizeitanlage mit Restaurant und Biergarten
Zielgruppe
Tennis- und Freizeitanlage mit Restaurant und Biergarten. Zielgruppe von Jung bis Alt
Aufgabenstellung
Speise- und Getränkekarte. Klassisch und klar strukturiert. Möglichst zum selbst ausdrucken (kein Randloses Design) Möglichkeit zum selbstständigen ändern als Word Dokument. A4 Format. Hülle der Speisekarte bereits vorhanden. Siehe Fotos
Wenn möglich farbiges Logo verwenden. Alternativ habe ich noch eine schwarz weiß Variante hinzugefügt.

```html
<!DOCTYPE html>
<html lang="de">
<head>
<meta charset="utf-8">
<title>Speisekarte – Seewinkel</title>
<link href="https://fonts.googleapis.com/css2?family=Playfair+Display:wght@400;500&family=Inter:wght@400&display=swap" rel="stylesheet">
<style>
  :root {
    --bg: #eef0e3;
    --card-cream: #f3f5e8;
    --card-white: #ffffff;
    --green: #1f4a33;
    --text: #2c3a31;
    --line: #53675a;
    --photo-a: #2f5a3e;
    --photo-b: #b89a6a;
  }
  * { box-sizing: border-box; margin: 0; padding: 0; }
  html, body { width: 1200px; height: 900px; overflow: hidden; }
  body { background: var(--bg); position: relative; font-family: "Inter", sans-serif; color: var(--text); }

  .menu-card { position: absolute; box-shadow: 0 2px 8px rgba(0,0,0,0.12); }
  .menu-card .frame { position: absolute; inset: 0; width: 100%; height: 100%; }
  .menu-card .frame path { fill: none; stroke: var(--line); stroke-width: 1; }

  .back-page { left: 270px; top: 90px; width: 364px; height: 639px; background: var(--card-cream); }
  .back-page .photo {
    position: absolute; left: 92px; top: 144px; width: 187px; height: 189px;
    background: #fff; padding: 7px;
  }
  .back-page .photo div {
    width: 100%; height: 100%;
    background: linear-gradient(180deg, var(--photo-a) 0%, #4f6a4c 50%, var(--photo-b) 100%);
  }
  .back-page .title {
    position: absolute; left: 0; right: 0; top: 430px; text-align: center;
    font-family: "Playfair Display", serif; font-size: 17px; color: var(--text);
  }
  .back-page .tagline {
    position: absolute; left: 0; right: 0; top: 452px; text-align: center;
    font-size: 11px; line-height: 14px; color: var(--text);
  }
  .back-page .since {
    position: absolute; left: 0; right: 0; top: 525px; text-align: center; font-size: 11px;
  }
  .back-page .rule {
    position: absolute; left: 165px; width: 34px; top: 545px; border-top: 1px solid var(--line);
  }
  .back-page .hours {
    position: absolute; left: 0; right: 0; top: 550px; text-align: center; font-size: 11px; line-height: 15px;
  }

  .cover-page { left: 581px; top: 152px; width: 362px; height: 632px; background: var(--card-white); }
  .cover-page .brand {
    position: absolute; left: 0; right: 0; top: 250px; text-align: center;
    font-family: "Playfair Display", serif; font-size: 22px; font-weight: 500; color: var(--green);
  }
  .cover-page .title {
    position: absolute; left: 0; right: 0; top: 298px; text-align: center;
    font-family: "Playfair Display", serif; font-size: 34px; color: var(--green);
  }
  .cover-page .subtitle {
    position: absolute; left: 0; right: 0; top: 346px;
    display: flex; justify-content: center; align-items: center; gap: 8px;
    font-size: 13px; color: var(--text);
  }
  .cover-page .subtitle::before,
  .cover-page .subtitle::after { content: ""; width: 32px; border-top: 1px solid var(--line); }
</style>
</head>
<body>

<section class="menu-card back-page">
  <svg class="frame" viewBox="0 0 364 639">
    <path transform="translate(19 19)" d="M32 0 H294 A32 32 0 0 0 326 32 V569 A32 32 0 0 0 294 601 H32 A32 32 0 0 0 0 569 V32 A32 32 0 0 0 32 0 Z"/>
  </svg>
  <figure class="photo" role="img" aria-label="Foto: zwei Gäste mit Bier im Biergarten"><div></div></figure>
  <h2 class="title">Speisekarte</h2>
  <p class="tagline">Restaurant &amp;<br>Biergarten</p>
  <p class="since">Seit 1982</p>
  <div class="rule"></div>
  <p class="hours">Täglich<br>ab 11 Uhr</p>
</section>

<section class="menu-card cover-page">
  <svg class="frame" viewBox="0 0 362 632">
    <path transform="translate(20 20)" d="M32 0 H290 A32 32 0 0 0 322 32 V560 A32 32 0 0 0 290 592 H32 A32 32 0 0 0 0 560 V32 A32 32 0 0 0 32 0 Z"/>
  </svg>
  <p class="brand">Seewinkel</p>
  <h1 class="title">Speisekarte</h1>
  <p class="subtitle">Frisch &amp; regional</p>
</section>

</body>
</html>
```